Personal Business Card design contest for freelance work

Include

Brenvola.net/in/DanielMWhitacre (as URL and/or QR Code)
Daniel Whitacre
(555) 218-9034
DanielMWhitacre@Pelmora.com
Houston, TX

Industry/Entity Type

Business

```html
<!DOCTYPE html>
<html lang="en">
<head>
<meta charset="utf-8">
<title>Daniel Whitacre – Business Card</title>
<link rel="stylesheet" href="https://fonts.googleapis.com/css2?family=Source+Sans+3:wght@400;600&display=swap">
<style>
  :root {
    --backdrop: #2b2b2b;
    --card-white: #ffffff;
    --card-blue: #148bcc;
    --accent-blue: #1585c6;
    --text-grey: #8c8c8c;
    --art-light-top: #eef1f4;
    --art-light-bottom: #d9dee3;
    --art-blue-top: #2a97d2;
    --art-blue-bottom: #0f78b3;
  }
  * { margin: 0; padding: 0; box-sizing: border-box; }
  html, body {
    width: 1200px; height: 900px; overflow: hidden;
    background: var(--backdrop);
    font-family: "Source Sans 3", "Myriad Pro", sans-serif;
  }
  .canvas { position: relative; width: 1200px; height: 900px; }
  .card { position: absolute; border-radius: 14px; overflow: hidden; }
  .card--front { left: 334px; top: 121px; width: 548px; height: 318px; background: var(--card-white); }
  .card--back { left: 326px; top: 505px; width: 556px; height: 323px; background: var(--card-blue); }

  .artwork { position: absolute; border-radius: 10px; }
  .card--front .artwork {
    left: 250px; top: 39px; width: 80px; height: 243px;
    background: linear-gradient(to bottom, var(--art-light-top), var(--art-light-bottom));
  }
  .card--back .artwork {
    left: 238px; top: 27px; width: 90px; height: 270px;
    background: linear-gradient(to bottom, var(--art-blue-top), var(--art-blue-bottom));
  }

  .address {
    position: absolute; left: 24px; top: 157px;
    font-size: 15.5px; line-height: 17px; color: var(--text-grey);
  }
  .contact-list {
    position: absolute; left: 22px; top: 232px;
    list-style: none; font-size: 13.5px; color: var(--text-grey);
  }
  .contact-list li { display: flex; align-items: center; height: 20.5px; white-space: nowrap; }
  .contact-list svg { width: 12px; height: 12px; margin-right: 8px; flex: none; fill: var(--accent-blue); }

  .identity { position: absolute; right: 24px; top: 183px; text-align: right; }
  .identity__name { font-size: 24px; font-weight: 600; color: var(--accent-blue); line-height: 30px; }
  .identity__title { font-size: 16.5px; font-weight: 400; color: var(--text-grey); line-height: 20px; }
</style>
</head>
<body>
<main class="canvas">
  <section class="card card--front">
    <div class="artwork" role="img" aria-label="Illustrated caricature of the card owner in a suit"></div>

    <p class="address">Houston, TX<br>United States</p>

    <ul class="contact-list">
      <li>
        <svg viewBox="0 0 12 12" aria-hidden="true"><path d="M1 4c0-2 2-3 5-3s5 1 5 3v1H8.5V3.8h-5V5H1zM2.5 6h7l1 4.5h-9z"/></svg>
        (555) 218-9034
      </li>
      <li>
        <svg viewBox="0 0 12 12" aria-hidden="true"><path d="M1 2.5h10v7H1z M1.5 3l4.5 3.5L10.5 3" stroke="#fff" stroke-width="1"/></svg>
        DanielMWhitacre@Pelmora.com
      </li>
      <li>
        <svg viewBox="0 0 12 12" aria-hidden="true"><path d="M5 7l2-2M4.2 5.8L2.6 7.4a1.6 1.6 0 002.2 2.2l1.6-1.6M7.8 6.2l1.6-1.6a1.6 1.6 0 00-2.2-2.2L5.6 4" fill="none" stroke="#1585c6" stroke-width="1.4" stroke-linecap="round"/></svg>
        Brenvola.net/in/DanielMWhitacre
      </li>
    </ul>

    <div class="identity">
      <h1 class="identity__name">Daniel Whitacre</h1>
      <p class="identity__title">Managing Director</p>
    </div>
  </section>

  <section class="card card--back">
    <div class="artwork" role="img" aria-label="Illustrated caricature of the card owner in a suit"></div>
  </section>
</main>
</body>
</html>
```